Request for Business Card Design

Hi. My name is Marlene, I am looking for a new business card design for my company, Quarrow Signal Instruments, LLC. I really like the design you did for Tarsel Venture and was hoping you could do something similar using our full logo and our mark. I am also open to any raised texture design using our mark. I have attached our full logo, which would need to be somewhere on the card, as well as the mark in both outline and full form, as well as our brand colors / guide. The card does not have to be white, as long as our logo and mark appear. I actually like darker colored business cards more, but am open to all options. If you are interested in working with me, please let me know. We would also take the business card design into letterhead design if you can do that.

```html
<!DOCTYPE html>
<html lang="en">
<head>
<meta charset="utf-8">
<title>Quarrow Signal Instruments — Business Card</title>
<link href="https://fonts.googleapis.com/css2?family=Montserrat:wght@400;500;700&display=swap" rel="stylesheet">
<style>
  :root {
    --brand-blue: #0c9ac2;
    --ink-grey: #4a4a4c;
    --paper: #ffffff;
    --stage: #2a2a2c;
  }
  * { box-sizing: border-box; margin: 0; padding: 0; }
  html, body {
    width: 1200px; height: 880px; overflow: hidden;
    background: var(--stage);
    font-family: "Montserrat", Arial, sans-serif;
  }
  .card {
    position: absolute; left: 250px;
    width: 700px; height: 400px; overflow: hidden;
  }
  .card--front { top: 25px; background: var(--brand-blue); }
  .card--back { top: 455px; background: var(--paper); }

  .brand { position: absolute; display: flex; align-items: center; gap: 18px; }
  .brand__dot { border-radius: 50%; flex: none; }
  .brand__name { font-weight: 700; line-height: 1; letter-spacing: 2px; }
  .brand__name span { display: block; font-size: 0.34em; letter-spacing: 1.6px; margin-top: 6px; }

  .card--front .brand { left: 150px; top: 150px; }
  .card--front .brand__dot { width: 70px; height: 70px; background: var(--paper); }
  .card--front .brand__name { color: var(--paper); font-size: 58px; }

  .card--back .brand { left: 55px; top: 140px; }
  .card--back .brand__dot { width: 50px; height: 50px; background: var(--brand-blue); }
  .card--back .brand__name { color: var(--ink-grey); font-size: 40px; }

  .swoosh { position: absolute; inset: 0; }

  .divider {
    position: absolute; left: 388px; top: 76px;
    width: 2px; height: 160px; background: var(--brand-blue);
  }
  .contact { position: absolute; left: 408px; top: 70px; color: #222; }
  .contact__name { font-size: 22px; font-weight: 700; color: var(--ink-grey); letter-spacing: 0.5px; line-height: 1.2; }
  .contact__name em { font-style: normal; color: var(--brand-blue); }
  .contact__role { font-size: 16px; margin: 4px 0 14px; }
  .contact__list { list-style: none; }
  .contact__item { display: flex; align-items: center; gap: 10px; font-size: 15px; line-height: 1.2; margin-bottom: 8px; }
  .contact__icon { width: 16px; height: 16px; flex: none; fill: var(--brand-blue); }
</style>
</head>
<body>

<section class="card card--front" aria-label="Card front">
  <div class="brand">
    <div class="brand__dot"></div>
    <div class="brand__name">QUARROW<span>SIGNAL INSTRUMENTS</span></div>
  </div>
</section>

<section class="card card--back" aria-label="Card back">
  <svg class="swoosh" viewBox="0 0 700 400" aria-hidden="true">
    <path d="M0 400 L0 352 Q450 346 700 262 L700 400 Z" fill="var(--brand-blue)"/>
    <path d="M170 334 Q470 314 680 250 Q480 326 170 338 Z" fill="var(--ink-grey)"/>
  </svg>

  <div class="brand">
    <div class="brand__dot"></div>
    <div class="brand__name">QUARROW<span>SIGNAL INSTRUMENTS</span></div>
  </div>

  <div class="divider"></div>

  <div class="contact">
    <p class="contact__name">JONAH <em>PELLARY</em></p>
    <p class="contact__role">Owner</p>
    <ul class="contact__list">
      <li class="contact__item">
        <svg class="contact__icon" viewBox="0 0 16 16"><path d="M3 1h3l1.5 4-2 1.2a9 9 0 0 0 4.3 4.3L11 8.5l4 1.5v3a2 2 0 0 1-2 2A12 12 0 0 1 1 3a2 2 0 0 1 2-2z"/></svg>
        555.014.2290
      </li>
      <li class="contact__item">
        <svg class="contact__icon" viewBox="0 0 16 16"><path d="M1 3h14v10H1z M2 4l6 5 6-5" stroke="#fff" stroke-width="1"/></svg>
        info@quarrowsignal.com
      </li>
      <li class="contact__item">
        <svg class="contact__icon" viewBox="0 0 16 16"><circle cx="8" cy="8" r="7"/><path d="M1 8h14M8 1c-3 3-3 11 0 14M8 1c3 3 3 11 0 14" stroke="#fff" stroke-width="1" fill="none"/></svg>
        www.quarrowsignal.com
      </li>
    </ul>
  </div>
</section>

</body>
</html>
```